MRT Property - Business Cards

Looking for a business card & general letterhead, signage etc design for our new logo.

Colours:
000a20
0056a2
00b5ef
0088ce
68cef2

Fonts:
Poppins
Karla

Please keep look and feel of new brand - example in the zip package I sent.

```html
<!DOCTYPE html>
<html lang="en">
<head>
<meta charset="utf-8">
<title>MRT Property – Business Cards</title>
<link rel="stylesheet" href="https://fonts.googleapis.com/css2?family=Karla:wght@400;500&family=Poppins:wght@400;600;700&display=swap">
<style>
  :root {
    --navy: #000a20;
    --card-dark: #0b1020;
    --blue: #0056a2;
    --sky: #00b5ef;
    --mid: #0088ce;
    --light: #68cef2;
    --white: #ffffff;
    --backdrop: #2a2a2c;
  }
  * { margin: 0; padding: 0; box-sizing: border-box; }
  html, body { width: 1200px; height: 880px; overflow: hidden; }
  body {
    background: var(--backdrop);
    font-family: "Karla", sans-serif;
    position: relative;
  }
  .card {
    position: absolute;
    left: 250px;
    width: 700px;
    height: 400px;
    border-radius: 30px;
    overflow: hidden;
  }
  .card--front { top: 20px; background: var(--blue); }
  .card--back { top: 460px; background: var(--card-dark); }

  .brand {
    position: absolute;
    display: flex;
    align-items: center;
    font-family: "Poppins", sans-serif;
    font-weight: 700;
    white-space: nowrap;
  }
  .brand__dot { border-radius: 50%; flex: none; }
  .card--front .brand {
    left: 50%; top: 50%;
    transform: translate(-50%, -50%);
    font-size: 72px;
    color: var(--white);
    gap: 26px;
  }
  .card--front .brand__dot { width: 64px; height: 64px; background: var(--white); }
  .card--back .brand {
    left: 48px; top: 56px;
    font-size: 40px;
    color: var(--blue);
    gap: 16px;
  }
  .card--back .brand__dot { width: 38px; height: 38px; background: var(--sky); }

  .holder {
    position: absolute;
    right: 34px;
    top: 40px;
    text-align: right;
  }
  .holder__name {
    font-family: "Poppins", sans-serif;
    font-weight: 600;
    font-size: 24px;
    letter-spacing: 1px;
    color: var(--blue);
    line-height: 1.2;
  }
  .holder__role {
    font-family: "Poppins", sans-serif;
    font-weight: 400;
    font-size: 15px;
    color: var(--white);
    letter-spacing: .5px;
  }
  .accent-bar {
    position: absolute;
    right: 14px;
    top: 40px;
    width: 8px;
    height: 54px;
    background: var(--blue);
  }

  .contact {
    position: absolute;
    left: 60px;
    bottom: 38px;
    color: var(--white);
    font-family: "Poppins", sans-serif;
    font-size: 17px;
    line-height: 1.4;
  }
  .contact__address { margin-bottom: 26px; }
  .contact__list { list-style: none; }
  .contact__item { display: flex; align-items: center; gap: 10px; }
  .contact__icon { width: 16px; height: 16px; flex: none; fill: var(--sky); }
</style>
</head>
<body>
  <section class="card card--front" aria-label="Business card front">
    <div class="brand"><span class="brand__dot"></span>MRT Property</div>
  </section>

  <section class="card card--back" aria-label="Business card back">
    <div class="brand"><span class="brand__dot"></span>MRT Property</div>

    <div class="holder">
      <p class="holder__name">DANIEL REEVE</p>
      <p class="holder__role">Managing Director</p>
    </div>
    <span class="accent-bar"></span>

    <div class="contact">
      <p class="contact__address">Your address, City<br>State, Zip 1234</p>
      <ul class="contact__list">
        <li class="contact__item">
          <svg class="contact__icon" viewBox="0 0 16 16" aria-hidden="true"><path d="M3.6 1.2 6 3.6 4.8 5.4c.8 1.9 2.1 3.2 4 4l1.8-1.2 2.4 2.4-1.6 2.2C6.4 12.6 2.6 8.6 1.4 2.8z"/></svg>
          123 456 789
        </li>
        <li class="contact__item">
          <svg class="contact__icon" viewBox="0 0 16 16" aria-hidden="true"><path d="M1 3h14v10H1zm1.4 1.2L8 8.6l5.6-4.4z"/></svg>
          info@yourgmail.com
        </li>
        <li class="contact__item">
          <svg class="contact__icon" viewBox="0 0 16 16" aria-hidden="true"><circle cx="8" cy="8" r="7"/><path d="M1 8h14M8 1c-3 3.5-3 10.5 0 14M8 1c3 3.5 3 10.5 0 14" stroke="#0b1020" stroke-width="1" fill="none"/></svg>
          www.yourwebsite.com
        </li>
      </ul>
    </div>
  </section>
</body>
</html>
```